Animal Eye Clinic needs a Business card

We are a new veterinary ophthalmology practice (Ridgeline Pet Vision Care) and we need a business card designed. We only see animal eyes - we are not a regular veterinary clinic. We already have a logo. We are looking for a professional, good looking business card to hand out to our clients. We are looking for something simple but professional and contemporary. Our logo is likely the only picture/graphic that needs to be on the card.
Updates

Contact Information for Business Card

Delia Vossman, BSc, DVM, MSc, DipACVO
Veterinary Ophthalmologist

Phone: 250.418.3927
Email: ridgelinepetvisioncare@mailbox-example.net
Website: ridgelinepetvisioncare-example.net
Address: 1874 Thornbury Rd
Kelowna, BC, V1X 4M9

Colors

Designer to choose colors to be used in the design.

Requirements
Must have
• Our logo (attached)

```html
<!DOCTYPE html>
<html lang="en">
<head>
<meta charset="utf-8">
<title>Ridgeline Pet Vision Care – Business Card</title>
<link href="https://fonts.googleapis.com/css2?family=Open+Sans:wght@400;600;700&display=swap" rel="stylesheet">
<style>
  :root {
    --teal: #0597a8;
    --teal-soft: #bfe4e9;
    --grey-text: #5c5f62;
    --grey-light: #8a8d90;
    --card: #ffffff;
    --backdrop: #d9dadb;
  }
  * { box-sizing: border-box; margin: 0; padding: 0; }
  html, body { width: 1200px; height: 800px; overflow: hidden; }
  body {
    background: var(--backdrop);
    font-family: "Open Sans", Arial, sans-serif;
    position: relative;
  }
  .card {
    position: absolute;
    width: 560px;
    height: 320px;
    background: var(--card);
    box-shadow: 0 10px 28px rgba(0,0,0,0.18);
    overflow: hidden;
  }
  .card--front { left: 50px; top: 90px; }
  .card--back { left: 590px; top: 390px; }

  /* Front */
  .artwork {
    position: absolute;
    left: 0; bottom: 0;
    width: 250px; height: 240px;
    background: radial-gradient(circle at 40% 60%, var(--teal-soft), rgba(191,228,233,0) 75%);
  }
  .brand-name {
    font-weight: 700;
    color: var(--teal);
    text-transform: uppercase;
    letter-spacing: 0.04em;
    line-height: 1.1;
  }
  .card--front .brand-name {
    position: absolute;
    right: 34px; top: 30px;
    font-size: 22px;
    text-align: right;
  }
  .contact {
    position: absolute;
    left: 250px; top: 118px;
    color: var(--grey-text);
    font-size: 12.5px;
    line-height: 1.55;
  }
  .contact__name {
    color: var(--teal);
    font-weight: 700;
    font-size: 15px;
  }
  .contact__credentials {
    font-weight: 400;
    font-size: 10.5px;
  }
  .contact__row { display: flex; align-items: center; gap: 7px; }
  .contact__row svg { width: 11px; height: 11px; flex: none; fill: var(--teal); }

  /* Back */
  .back-brand {
    position: absolute;
    left: 70px; top: 110px;
    display: flex; align-items: center; gap: 18px;
  }
  .back-brand__dot {
    width: 62px; height: 62px; border-radius: 50%;
    background: var(--teal);
    flex: none;
  }
  .card--back .brand-name { font-size: 28px; }
  .website {
    position: absolute;
    left: 0; right: 0; bottom: 40px;
    text-align: center;
    color: var(--grey-text);
    font-size: 14px;
    letter-spacing: 0.22em;
  }
</style>
</head>
<body>
  <section class="card card--front">
    <div class="artwork" role="img" aria-label="Clinic artwork area in teal and grey tones"></div>
    <h1 class="brand-name">Ridgeline<br>Pet Vision Care</h1>
    <div class="contact">
      <p class="contact__name">Delia Vossman, <span class="contact__credentials">BSc, DVM, MSc, DipACVO</span></p>
      <p>Veterinary Ophthalmologist</p>
      <p>1874 Thornbury Rd Kelowna, BC, V1X 4M9</p>
      <p class="contact__row">
        <svg viewBox="0 0 24 24" aria-hidden="true"><path d="M6.6 10.8a15.2 15.2 0 0 0 6.6 6.6l2.2-2.2a1 1 0 0 1 1-.25 11.4 11.4 0 0 0 3.6.57 1 1 0 0 1 1 1V20a1 1 0 0 1-1 1A17 17 0 0 1 3 4a1 1 0 0 1 1-1h3.5a1 1 0 0 1 1 1c0 1.25.2 2.45.57 3.57a1 1 0 0 1-.25 1z"/></svg>
        250.418.3927
      </p>
      <p class="contact__row">
        <svg viewBox="0 0 24 24" aria-hidden="true"><path d="M2 5h20v14H2z M3.5 6.5 12 13l8.5-6.5" stroke="#fff" stroke-width="1.6"/></svg>
        ridgelinepetvisioncare@mailbox-example.net
      </p>
      <p class="contact__row">
        <svg viewBox="0 0 24 24" aria-hidden="true"><circle cx="12" cy="12" r="10"/></svg>
        ridgelinepetvisioncare-example.net
      </p>
    </div>
  </section>

  <section class="card card--back">
    <div class="back-brand">
      <span class="back-brand__dot" aria-hidden="true"></span>
      <p class="brand-name">Ridgeline<br>Pet Vision Care</p>
    </div>
    <p class="website">www.ridgelinepetvisioncare-example.net</p>
  </section>
</body>
</html>
```